Business card design and logo needed please help

I need a card for a new plumbing business. i want double sided gloss and on the front i need an attractive logo for my business the incorperates a rhino and plumbing to go with my name aswell as my contact info. logo aswell has to be not out there but remeberable as it will be representing this later to be large Business.Could also incorperate the initials of my buisness being TLC. On the back i want the type of work that i undertake, Plumbing, Maintaince, gasfitting and certification, sanitary drainage and stormwater, drain cleaning, All hot water systems installations and repair , FREE QUOTE is needed to stand out aswell. i like an indate colour design but more then one colour like black and grey or anything.info has to be easy to read that will draw in all types of clients. want a slogan on it saying "tough on Quality" aswell. Email aswell has changed to make it easier for people. Its now( Tlcadvisory@fernmail.test)
Industry/Entity Type
Business
Contact Information for Business Card
Borlo's Plumbing and Gas Fitting, Dale Marchetti, QBSA No. 48 07 316, ABN No. 74 205 913 480, Email. Borlosplumbingandgasfitting@fernmail.test, Mobile no. 0491 630 578
Logo styles of interest
Pictorial/Combination Logo
Abstract Logo
Character Logo
Look and feel

```html
<!DOCTYPE html>
<html lang="en">
<head>
<meta charset="utf-8">
<title>TLC – Services Card</title>
<link rel="stylesheet" href="https://fonts.googleapis.com/css2?family=Cabin+Condensed:wght@400;600;700&display=swap">
<style>
  :root {
    --paper: #ffffff;
    --teal: #3aa9c5;
    --mint: #b0e6de;
    --ink: #111111;
    --shade: rgba(0, 0, 0, 0.28);
  }
  html, body {
    margin: 0;
    padding: 0;
    overflow: hidden;
    background: var(--paper);
  }
  .card {
    position: relative;
    width: 1200px;
    height: 741px;
    overflow: hidden;
    background: var(--paper);
    font-family: "Cabin Condensed", "Arial Narrow", sans-serif;
  }
  .wave {
    position: absolute;
    inset: 0;
    width: 1200px;
    height: 741px;
  }
  .wave__band { fill: var(--teal); }
  .wave__field { fill: var(--mint); }
  .wave__group { filter: drop-shadow(0 -4px 6px var(--shade)); }

  .headline {
    position: absolute;
    left: 631px;
    top: 84px;
    transform: translateX(-50%);
    margin: 0;
    font-size: 45px;
    font-weight: 700;
    letter-spacing: 0.5px;
    color: var(--teal);
    white-space: nowrap;
    text-shadow: 0 2px 2px rgba(0, 0, 0, 0.25);
  }

  .brand {
    position: absolute;
    left: 110px;
    top: 250px;
    width: 360px;
    display: flex;
    flex-direction: column;
    align-items: center;
  }
  .brand__dot {
    width: 130px;
    height: 130px;
    border-radius: 50%;
    background: var(--teal);
  }
  .brand__name {
    margin: 4px 0 0;
    font-size: 175px;
    line-height: 1;
    font-weight: 600;
    color: var(--teal);
    letter-spacing: 2px;
  }

  .services {
    position: absolute;
    right: 35px;
    top: 218px;
    margin: 0;
    padding: 0;
    list-style: none;
    text-align: right;
    font-size: 50px;
    line-height: 59px;
    font-weight: 400;
    color: var(--ink);
  }
  .services__initial { font-weight: 700; }
</style>
</head>
<body>
<div class="card">
  <svg class="wave" viewBox="0 0 1200 741" aria-hidden="true">
    <g class="wave__group">
      <path class="wave__band" d="M0,573 C250,560 420,520 560,430 C720,320 820,170 980,120 C1080,88 1150,80 1200,76 L1200,741 L0,741 Z"/>
      <path class="wave__field" d="M0,579 C260,567 430,532 572,446 C732,346 842,212 992,162 C1092,130 1160,122 1200,122 L1200,741 L0,741 Z"/>
    </g>
  </svg>

  <h1 class="headline">CALL FOR FREE QUOTE</h1>

  <div class="brand">
    <div class="brand__dot"></div>
    <p class="brand__name">TLC</p>
  </div>

  <ul class="services">
    <li><span class="services__initial">P</span>lumbing</li>
    <li>installations</li>
    <li>&amp; maintenance</li>
    <li><span class="services__initial">S</span>tormwater &amp; tanks</li>
    <li><span class="services__initial">D</span>rain cleaning services</li>
    <li><span class="services__initial">S</span>anitary drainage &amp; repairs</li>
    <li><span class="services__initial">H</span>ot water system Installations &amp; repairs</li>
    <li><span class="services__initial">G</span>as fitting Installation, repairs and Certification</li>
  </ul>
</div>
</body>
</html>
```